business card - Helicopter Flight Services, Flight School, etc.

We need a business card design for a new helicopter service.

We offer Helicopter Flight Services, Aerial Filming & Photography, Flight School, and Helicopter Tours. In that order.

Summit BladeAir, Inc.
Dennis Tollerby
SummitBladeair@Kestmail.com
626-418-7352

Based at the Brenwick Airport in Van Nuys, CA. The final design should communicate integrity and safety. Pictures or logos at your discretion.

Card back side - surprise me.

```html
<!DOCTYPE html>
<html lang="en">
<head>
<meta charset="utf-8">
<title>Summit BladeAir, Inc. – Business Card</title>
<link rel="stylesheet" href="https://fonts.googleapis.com/css2?family=Open+Sans:wght@400;600;700;800&display=swap">
<style>
  :root {
    --blue-deep: #1a5fb4;
    --blue-mid: #2c86d4;
    --blue-light: #4fb0e6;
    --green: #8cc63f;
    --white: #ffffff;
    --stage: #e9ecef;
    --ink-blue: #1d63b8;
  }
  * { box-sizing: border-box; margin: 0; padding: 0; }
  html, body { width: 1200px; height: 913px; overflow: hidden; }
  body {
    background: var(--stage);
    font-family: "Open Sans", Arial, sans-serif;
    position: relative;
  }
  .card {
    position: absolute;
    width: 560px;
    height: 320px;
    top: 296px;
    overflow: hidden;
    box-shadow: 0 6px 18px rgba(0,0,0,.18);
  }
  .brand {
    display: flex;
    align-items: center;
    gap: 12px;
    font-weight: 800;
    text-transform: uppercase;
    line-height: 1.05;
  }
  .brand-dot {
    flex: none;
    border-radius: 50%;
    background: var(--green);
  }

  /* ---------- Front ---------- */
  .card-front {
    left: 30px;
    background: linear-gradient(160deg, var(--blue-light) 0%, var(--blue-mid) 45%, var(--blue-deep) 100%);
  }
  .front-strip {
    position: absolute;
    left: 70px; top: 110px;
    width: 150px; height: 210px;
    background: var(--white);
  }
  .front-brand {
    position: absolute;
    left: 250px; top: 58px;
    color: var(--white);
    font-size: 26px;
  }
  .front-brand .brand-dot { width: 14px; height: 14px; }
  .contact {
    position: absolute;
    left: 250px; top: 178px;
    color: var(--white);
  }
  .contact-name { font-weight: 700; font-size: 19px; }
  .contact-role { color: var(--green); font-size: 12px; margin-bottom: 10px; }
  .contact-line {
    display: flex; align-items: center; gap: 7px;
    font-size: 13px; line-height: 1.6;
  }
  .contact-line svg { width: 12px; height: 12px; fill: var(--green); flex: none; }

  /* ---------- Back ---------- */
  .card-back {
    left: 610px;
    background: var(--white);
  }
  .back-brand {
    position: absolute;
    left: 40px; top: 52px;
    color: var(--ink-blue);
    font-size: 32px;
  }
  .back-brand .brand-dot { width: 16px; height: 16px; }
  .back-band {
    position: absolute;
    left: 0; right: 0; bottom: 0; height: 150px;
    background: linear-gradient(160deg, var(--blue-mid) 0%, var(--blue-deep) 100%);
  }
  .services {
    position: absolute;
    left: 44px; bottom: 28px;
    list-style: none;
    color: var(--white);
    font-size: 14px;
    line-height: 1.6;
  }
  .services li { display: flex; align-items: center; gap: 9px; }
  .services li::before {
    content: ""; width: 9px; height: 9px; border-radius: 50%;
    background: var(--green); flex: none;
  }
</style>
</head>
<body>
  <section class="card card-front" aria-label="Business card front">
    <div class="front-strip"></div>
    <div class="brand front-brand">
      <span class="brand-dot"></span>
      <span>Summit<br>BladeAir, Inc.</span>
    </div>
    <div class="contact">
      <p class="contact-name">Dennis Tollerby</p>
      <p class="contact-role">Owner</p>
      <p class="contact-line">
        <svg viewBox="0 0 24 24" aria-hidden="true"><path d="M6.6 10.8a15.1 15.1 0 0 0 6.6 6.6l2.2-2.2c.3-.3.7-.4 1-.2 1.1.4 2.3.6 3.6.6.6 0 1 .4 1 1V20c0 .6-.4 1-1 1A17 17 0 0 1 3 4c0-.6.4-1 1-1h3.5c.6 0 1 .4 1 1 0 1.3.2 2.5.6 3.6.1.3 0 .7-.2 1z"/></svg>
        626-418-7352
      </p>
      <p class="contact-line">
        <svg viewBox="0 0 24 24" aria-hidden="true"><path d="M2 5h20v14H2zm2 2v.5l8 5 8-5V7zm0 2.8V17h16V9.8l-8 5z"/></svg>
        SummitBladeair@Kestmail.com
      </p>
    </div>
  </section>

  <section class="card card-back" aria-label="Business card back">
    <div class="brand back-brand">
      <span class="brand-dot"></span>
      <span>Summit<br>BladeAir, Inc.</span>
    </div>
    <div class="back-band"></div>
    <ul class="services">
      <li>Helicopter Flight Services</li>
      <li>Aerial Filming &amp; Photography</li>
      <li>Flight School</li>
      <li>Helicopter Tours</li>
    </ul>
  </section>
</body>
</html>
```